Verdant Systems Business Card

want the back of card to be blue- with the logo in the center
front of card- info plus logo (info being mailing address, email address, and website address )
4 different names with titles to have on cards
1) Calvin Borsted - Owner
2) Naomi Trelvik- Customer Relationship Specialist
3) Felix Andrade- Vice President of Sales
4) Owen Markby- Chief Technology Officer

Target Market(s)

tech company in the government/probation office industry

Industry/Entity Type

Government Office

Contact Information for Business Card

1) Calvin Borsted - Owner

Colors
0355a3
ffffff

Requirements
Must have
• back side should be blue, with the logo placed in the center
• front side needs to include both the logo, as well as company info (info should include website address, email address, and mailing address)

```html
<!DOCTYPE html>
<html lang="en">
<head>
<meta charset="utf-8">
<title>Verdant Systems Business Cards</title>
<link rel="stylesheet" href="https://fonts.googleapis.com/css2?family=Open+Sans:wght@400;600;700&family=Roboto:wght@700&display=swap">
<style>
  :root {
    --navy: #1a2e55;
    --grey-stripe: #8a8d92;
    --stage: #c5c8cc;
    --white: #ffffff;
    --ink: #333a45;
  }
  * { margin: 0; padding: 0; box-sizing: border-box; }
  html, body {
    width: 1200px; height: 900px; overflow: hidden;
    background: var(--stage);
    font-family: "Open Sans", Arial, sans-serif;
  }
  .stage { position: relative; width: 1200px; height: 900px; }

  .card {
    position: absolute;
    border-radius: 22px;
    overflow: hidden;
    box-shadow: 0 4px 10px rgba(0,0,0,0.25);
  }
  .card--front { left: 56px; width: 454px; height: 259px; background: var(--white); }
  .card--front.one { top: 36px; }
  .card--front.two { top: 327px; }
  .card--front.three { top: 619px; }

  .brand {
    position: absolute; left: 20px; top: 92px; width: 160px;
    display: flex; flex-direction: column; align-items: center; gap: 8px;
  }
  .brand__mark { width: 14px; height: 14px; background: var(--navy); }
  .brand__name {
    color: var(--navy); font-weight: 700; font-size: 21px; line-height: 1.1;
    text-align: center;
  }

  .divider {
    position: absolute; left: 227px; top: 70px; width: 1.5px; height: 118px;
    background: var(--navy);
  }
  .info { position: absolute; left: 245px; top: 64px; color: var(--ink); }
  .info__name { color: var(--navy); font-weight: 700; font-size: 13.5px; line-height: 18px; }
  .info__title { font-size: 11.5px; line-height: 15px; margin-bottom: 2px; }
  .info__address { font-size: 11.5px; line-height: 13.5px; margin-bottom: 5px; }
  .contact { list-style: none; font-size: 11.5px; line-height: 14.8px; }
  .contact li { display: flex; align-items: center; gap: 8px; }
  .contact svg { width: 8px; height: 8px; fill: var(--navy); flex: none; }

  .wave { position: absolute; left: 0; bottom: 0; width: 454px; height: 50px; }

  .card--back {
    left: 584px; top: 296px; width: 567px; height: 323px;
    background: var(--navy);
    display: flex; flex-direction: column; align-items: center; justify-content: center; gap: 14px;
  }
  .card--back .brand__mark { width: 22px; height: 22px; background: var(--white); }
  .card--back .brand__name { color: var(--white); font-size: 40px; }

  .note {
    position: absolute; left: 575px; top: 720px; width: 600px;
    font-family: "Roboto", Arial, sans-serif; font-weight: 700;
    font-size: 21.5px; line-height: 27px; color: var(--navy);
  }
</style>
</head>
<body>
<main class="stage">

  <!-- Front: Calvin Borsted -->
  <section class="card card--front one">
    <div class="brand"><span class="brand__mark"></span><span class="brand__name">Verdant Systems</span></div>
    <div class="divider"></div>
    <div class="info">
      <p class="info__name">Calvin Borsted</p>
      <p class="info__title">Owner</p>
      <p class="info__address">Larkfield Crossing<br>Ostrava Heights, 2047</p>
      <ul class="contact">
        <li><svg viewBox="0 0 10 10"><path d="M2 0h2l1 2.5-1.3 1a5 5 0 0 0 2.8 2.8l1-1.3L10 6v2a2 2 0 0 1-2 2A8 8 0 0 1 0 2a2 2 0 0 1 2-2z"/></svg>555-204-7731</li>
        <li><svg viewBox="0 0 10 10"><path d="M2.5 0h5v10h-5zM3.5 1v7h3V1z"/></svg>555-204-7790(office)</li>
        <li><svg viewBox="0 0 10 10"><path d="M0 1.5h10v7H0zM1 2.5l4 3 4-3v-.2H1z"/></svg>info@verdantsystems.net</li>
        <li><svg viewBox="0 0 10 10"><circle cx="5" cy="5" r="5"/></svg>www.verdantsystems.net</li>
      </ul>
    </div>
    <svg class="wave" viewBox="0 0 454 50" preserveAspectRatio="none">
      <path d="M0 6 C120 26 220 22 300 10 C360 2 420 2 454 6 V12 C420 9 360 9 300 16 C220 28 110 30 0 12 Z" fill="var(--navy)"/>
      <path d="M0 14 C110 32 220 30 300 18 C360 11 420 11 454 14 V18 C420 15 360 15 300 22 C220 34 110 36 0 20 Z" fill="var(--grey-stripe)"/>
      <path d="M0 22 C110 38 220 36 300 24 C360 17 420 17 454 20 V50 H0 Z" fill="var(--navy)"/>
    </svg>
  </section>

  <!-- Front: Naomi Trelvik -->
  <section class="card card--front two">
    <div class="brand"><span class="brand__mark"></span><span class="brand__name">Verdant Systems</span></div>
    <div class="divider"></div>
    <div class="info">
      <p class="info__name">Naomi Trelvik</p>
      <p class="info__title">Customer Relationship Specialist</p>
      <p class="info__address">Larkfield Crossing<br>Ostrava Heights, 2047</p>
      <ul class="contact">
        <li><svg viewBox="0 0 10 10"><path d="M2 0h2l1 2.5-1.3 1a5 5 0 0 0 2.8 2.8l1-1.3L10 6v2a2 2 0 0 1-2 2A8 8 0 0 1 0 2a2 2 0 0 1 2-2z"/></svg>555-204-7731</li>
        <li><svg viewBox="0 0 10 10"><path d="M2.5 0h5v10h-5zM3.5 1v7h3V1z"/></svg>555-204-7790(office)</li>
        <li><svg viewBox="0 0 10 10"><path d="M0 1.5h10v7H0zM1 2.5l4 3 4-3v-.2H1z"/></svg>info@verdantsystems.net</li>
        <li><svg viewBox="0 0 10 10"><circle cx="5" cy="5" r="5"/></svg>www.verdantsystems.net</li>
      </ul>
    </div>
    <svg class="wave" viewBox="0 0 454 50" preserveAspectRatio="none">
      <path d="M0 6 C120 26 220 22 300 10 C360 2 420 2 454 6 V12 C420 9 360 9 300 16 C220 28 110 30 0 12 Z" fill="var(--navy)"/>
      <path d="M0 14 C110 32 220 30 300 18 C360 11 420 11 454 14 V18 C420 15 360 15 300 22 C220 34 110 36 0 20 Z" fill="var(--grey-stripe)"/>
      <path d="M0 22 C110 38 220 36 300 24 C360 17 420 17 454 20 V50 H0 Z" fill="var(--navy)"/>
    </svg>
  </section>

  <!-- Front: Felix Andrade -->
  <section class="card card--front three">
    <div class="brand"><span class="brand__mark"></span><span class="brand__name">Verdant Systems</span></div>
    <div class="divider"></div>
    <div class="info">
      <p class="info__name">Felix Andrade</p>
      <p class="info__title">Vice President of Sales</p>
      <p class="info__address">Larkfield Crossing<br>Ostrava Heights, 2047</p>
      <ul class="contact">
        <li><svg viewBox="0 0 10 10"><path d="M2 0h2l1 2.5-1.3 1a5 5 0 0 0 2.8 2.8l1-1.3L10 6v2a2 2 0 0 1-2 2A8 8 0 0 1 0 2a2 2 0 0 1 2-2z"/></svg>555-204-7731</li>
        <li><svg viewBox="0 0 10 10"><path d="M2.5 0h5v10h-5zM3.5 1v7h3V1z"/></svg>555-204-7790(office)</li>
        <li><svg viewBox="0 0 10 10"><path d="M0 1.5h10v7H0zM1 2.5l4 3 4-3v-.2H1z"/></svg>info@verdantsystems.net</li>
        <li><svg viewBox="0 0 10 10"><circle cx="5" cy="5" r="5"/></svg>www.verdantsystems.net</li>
      </ul>
    </div>
    <svg class="wave" viewBox="0 0 454 50" preserveAspectRatio="none">
      <path d="M0 6 C120 26 220 22 300 10 C360 2 420 2 454 6 V12 C420 9 360 9 300 16 C220 28 110 30 0 12 Z" fill="var(--navy)"/>
      <path d="M0 14 C110 32 220 30 300 18 C360 11 420 11 454 14 V18 C420 15 360 15 300 22 C220 34 110 36 0 20 Z" fill="var(--grey-stripe)"/>
      <path d="M0 22 C110 38 220 36 300 24 C360 17 420 17 454 20 V50 H0 Z" fill="var(--navy)"/>
    </svg>
  </section>

  <!-- Back -->
  <section class="card card--back">
    <span class="brand__mark"></span>
    <span class="brand__name">Verdant Systems</span>
  </section>

  <p class="note">I have made this card by using 3 different name . If you want i will make the card 4 different name and provide you all editable and print ready file.</p>

</main>
</body>
</html>
```